Design 4 pages for an event discovery website

This is a contest for the design of 4 pages for an events discovery website. The feature is part of the new sign-up process.

Please see the attached document for a full scope, mockups and the parent category icons.

Target Market(s)

18-35 Australian event goers

Industry/Entity Type

Events

Number of Pages Required

4 page

```html
<!DOCTYPE html>
<html lang="en">
<head>
<meta charset="utf-8">
<title>Lumiva – Sign Up</title>
<link href="https://fonts.googleapis.com/css2?family=Open+Sans:wght@400;600;700&display=swap" rel="stylesheet">
<style>
  :root {
    --text: #ffffff;
    --scene-dark: #1a1420;
    --scene-mid: #3a2238;
    --scene-glow: #6a2f5a;
    --rule: rgba(255,255,255,0.45);
    --search-blue: #0a6fd1;
    --action-green: #2db550;
    --social-blue-top: #2f86c8;
    --social-blue-bottom: #0d4f93;
    --social-divider: #8fd0ff;
    --footer-bg: #333233;
  }
  * { box-sizing: border-box; margin: 0; padding: 0; }
  html, body { width: 1200px; height: 795px; overflow: hidden; }
  body {
    position: relative;
    font-family: "Open Sans", Arial, sans-serif;
    color: var(--text);
    background: var(--scene-dark);
  }
  .hero-backdrop {
    position: absolute; left: 0; top: 0; width: 1200px; height: 704px;
    background:
      radial-gradient(circle at 470px 270px, rgba(200,120,220,0.35), transparent 120px),
      radial-gradient(ellipse at 350px 520px, var(--scene-glow), transparent 420px),
      radial-gradient(ellipse at 1000px 560px, #4a1a22, transparent 300px),
      linear-gradient(180deg, #1c1622 0%, var(--scene-mid) 55%, #241a24 100%);
  }
  .site-header {
    position: absolute; left: 0; top: 0; width: 1200px; height: 93px;
    border-bottom: 1px solid var(--rule);
  }
  .brand { position: absolute; left: 60px; top: 26px; }
  .brand-name { font-size: 28px; font-weight: 400; letter-spacing: 1px; line-height: 1; }
  .brand-tagline { font-size: 13px; margin-top: 9px; margin-left: 1px; }
  .search-box {
    position: absolute; left: 688px; top: 28px; width: 211px; height: 39px;
    background: var(--search-blue); border-radius: 2px;
    font-size: 13px; padding: 10px 0 0 19px;
  }
  .search-box svg { position: absolute; right: 9px; top: 11px; }
  .header-btn {
    position: absolute; top: 28px; width: 107px; height: 40px;
    background: var(--action-green); border-radius: 2px;
    font-size: 17px; font-weight: 600; text-align: center; line-height: 40px;
  }
  .btn-signup { left: 912px; }
  .btn-login { left: 1033px; }
  .signup-panel { position: absolute; left: 59px; top: 164px; }
  .signup-title { font-size: 24px; font-weight: 600; letter-spacing: 0.5px; }
  .social-connect {
    position: absolute; left: 2px; top: 53px; width: 362px; height: 76px;
    border-radius: 5px; display: flex; overflow: hidden;
    background: linear-gradient(180deg, var(--social-blue-top), var(--social-blue-bottom));
  }
  .social-connect-mark { width: 110px; display: flex; align-items: center; justify-content: center; }
  .social-connect-mark span { width: 22px; height: 22px; background: var(--text); border-radius: 2px; }
  .social-connect-divider { width: 5px; background: var(--social-divider); }
  .social-connect-label { flex: 1; font-size: 16px; font-weight: 700; line-height: 76px; padding-left: 15px; }
  .email-signup { position: absolute; left: 1px; top: 158px; font-size: 16px; white-space: nowrap; }
  .benefits { position: absolute; left: 528px; top: 174px; list-style: none; }
  .benefits li { position: relative; padding-left: 27px; font-size: 16px; height: 33.2px; white-space: nowrap; }
  .benefits li::before {
    content: ""; position: absolute; left: 0; top: 8px; width: 8px; height: 8px;
    border-radius: 50%; background: var(--text);
  }
  .site-footer {
    position: absolute; left: 0; top: 704px; width: 1200px; height: 91px;
    background: var(--footer-bg); text-align: center;
  }
  .social-links { display: flex; justify-content: center; gap: 4px; margin-top: 21px; }
  .social-links span { width: 22px; height: 22px; border-radius: 4px; background: var(--text); }
  .copyright { font-size: 12px; font-weight: 700; margin-top: 11px; }
</style>
</head>
<body>
  <div class="hero-backdrop" role="img" aria-label="Photo of friends celebrating at a party under falling confetti"></div>

  <header class="site-header">
    <div class="brand">
      <div class="brand-name">LUMIVA</div>
      <div class="brand-tagline">Find Events</div>
    </div>
    <div class="search-box">Search
      <svg width="17" height="17" viewBox="0 0 17 17" aria-hidden="true">
        <circle cx="7" cy="7" r="5" fill="none" stroke="#fff" stroke-width="2.5"/>
        <line x1="10.5" y1="10.5" x2="15" y2="15" stroke="#fff" stroke-width="3" stroke-linecap="round"/>
      </svg>
    </div>
    <div class="header-btn btn-signup">SIGN UP</div>
    <div class="header-btn btn-login">LOGIN</div>
  </header>

  <section class="signup-panel">
    <h1 class="signup-title">SIGN UP</h1>
    <div class="social-connect">
      <div class="social-connect-mark"><span></span></div>
      <div class="social-connect-divider"></div>
      <div class="social-connect-label">CONNECT WITH SOCIALHUB</div>
    </div>
    <p class="email-signup">Or else click here to signup in email account</p>
  </section>

  <ul class="benefits">
    <li>Get personalised event recommendations</li>
    <li>Get notified about your favourite events - never miss out again</li>
    <li>Follow all your favourite artists, musicians, teams and players in one place</li>
    <li>Follow your favourite local venues to know everything happening there</li>
    <li>Get curated news and feature content on your favourite artists (coming soon)</li>
    <li>Invite your mates to events via SocialHub (SH sign-up only)</li>
  </ul>

  <footer class="site-footer">
    <div class="social-links"><span></span><span></span><span></span><span></span><span></span></div>
    <p class="copyright">Copyright © 2015 lumiva. All Rights Reserved.</p>
  </footer>
</body>
</html>
```